Book Title: “Faith: Road of Endless Grace” Please see the attachment “Text on the cover”.

Book Cover Design Instructions: This book is meant for people of all religions and nationalities. Therefore, on the cover, there should be no mosque or an object specific to any religion. The primary emphasis should be on the "unconditional love of God." Therefore, use universal symbols of love. The second priority themes could be Sufism, Peace, and self-improvement. Rest is your imagination. Please also see the attachment: 'Book description and author's Bio.'
This book has the potential to be a best seller. Please do a good job.
What Book Cover Formats are required: A designer should submit cover designs in three formats: (1) eBook, (2) Paperback, and (3) Hardback. These books will be published on Borvex QPL.
Format requirements for eBooks are available from: https://qpl.borvex.example/en_US/help/topic/R731928457.
You can find paperback and hardback cover measurements from: https://qpl.borvex.example/en_US/cover-calculator
• To complete the project, all three formats should be accepted by Borvex QPL.
• The book interior trim size is 6.14 X 9.21 inches.
• Interior Type: Premium color.
• No bleed.
• I do not upload barcode. So, the back cover should have room for Borvex to print the barcode.
• Number of pages 126.
Compensation for the designer: After selecting one designer, I will increase the amount by $200 on Artvelle to compensate for three deliverables.
Follow-up of the Project:
After the book is published, I may need minor revisions. For example, the number of pages may change. Therefore, I will need the same design in revised sizes. In that case, I will pay $25 for each revision. For example, if the number of pages changes, I will need a different spine for paperback and hardback, then I will pay the artist $25 + $25 = $50 for both designs.
List of Enclosers:
1. Text on the cover.
2. Book description and author's Bio for the back cover.
3. Later, I will upload my picture for the book's back cover.

Target Market(s)

Any adult

Industry/Entity Type

Any industry

Requirements
Must have
• Three Deliverables

```html
<!DOCTYPE html>
<html lang="en">
<head>
<meta charset="utf-8">
<title>Faith: Road of Endless Grace — Cover Spread</title>
<link rel="stylesheet" href="https://fonts.googleapis.com/css2?family=Cinzel:wght@400;500&family=Crimson+Text:ital,wght@0,400;1,400&display=swap">
<style>
  :root {
    --stage: #1b1b1b;
    --ink-cream: #fbeeb0;
    --ink-gold: #f6dfa0;
    --ink-dark: #1e1206;
    --ink-bronze: #6a4a18;
    --glow-white: #fffdf4;
    --glow-yellow: #f7d36a;
    --glow-amber: #dd9a2c;
    --glow-orange: #b95f14;
    --shadow-brown: #4a2509;
    --deep-brown: #2a1305;
  }
  * { box-sizing: border-box; margin: 0; padding: 0; }
  html, body {
    width: 1200px; height: 1200px; overflow: hidden;
    background: var(--stage);
  }
  .canvas { position: relative; width: 1200px; height: 1200px; }

  .cover-spread {
    position: absolute; left: 127px; top: 39px;
    width: 945px; height: 675px; overflow: hidden;
  }
  .light-backdrop {
    position: absolute; inset: 0;
    background:
      radial-gradient(ellipse 360px 300px at 92% 2%, var(--glow-white) 0%, rgba(255,248,214,.85) 25%, rgba(247,211,106,0) 80%),
      radial-gradient(ellipse 620px 520px at 85% 25%, rgba(247,211,106,.95) 0%, rgba(221,154,44,.7) 45%, rgba(185,95,20,0) 85%),
      linear-gradient(150deg, var(--shadow-brown) 0%, #7a4512 30%, var(--glow-orange) 55%, var(--glow-amber) 72%, #c97a22 100%),
      linear-gradient(to bottom, rgba(0,0,0,0) 60%, rgba(42,19,5,.55) 100%);
    background-blend-mode: normal, normal, normal, multiply;
  }
  .light-backdrop::after {
    content: ""; position: absolute; inset: 0;
    background: linear-gradient(to right, rgba(42,19,5,.45) 0%, rgba(42,19,5,0) 48%),
                linear-gradient(to top, rgba(42,19,5,.5) 0%, rgba(42,19,5,0) 35%);
  }

  .back-cover, .spine, .front-cover { position: absolute; top: 0; height: 100%; }
  .back-cover { left: 0; width: 450px; text-align: center; color: var(--ink-cream); }
  .spine { left: 450px; width: 44px; }
  .front-cover { left: 494px; width: 451px; }

  .back-title {
    position: absolute; left: 0; width: 100%; top: 92px;
    font-family: "Cinzel", serif; font-weight: 400;
    font-size: 60px; line-height: 1; letter-spacing: 1px;
  }
  .back-subtitle {
    position: absolute; left: 0; width: 100%; top: 163px;
    font-family: "Cinzel", serif; font-size: 20px; letter-spacing: 1px;
  }
  .connector {
    font-family: "Crimson Text", serif; font-style: italic;
    text-transform: none; letter-spacing: 0; font-size: .9em;
  }
  .back-blurb {
    position: absolute; left: 50px; width: 350px; top: 196px;
    font-family: "Crimson Text", serif; font-size: 12.6px;
    line-height: 18.8px; letter-spacing: .3px;
  }
  .back-blurb p + p { margin-top: 18.8px; }

  .spine-title, .spine-author {
    position: absolute; left: 50%; writing-mode: vertical-rl;
    transform: translateX(-50%); white-space: nowrap;
    color: var(--ink-cream);
  }
  .spine-title {
    top: 36px; font-family: "Cinzel", serif; font-size: 17px; letter-spacing: 1px;
  }
  .spine-title .spine-main { font-size: 26px; }
  .spine-author {
    top: 484px; font-family: "Crimson Text", serif; font-size: 16px; letter-spacing: 2px;
  }

  .front-title {
    position: absolute; left: 0; width: 451px; top: 122px; text-align: center;
    font-family: "Cinzel", serif; font-weight: 500;
    font-size: 132px; line-height: 1; letter-spacing: -1px;
    background: linear-gradient(100deg, var(--ink-dark) 0%, #2b1a08 45%, var(--ink-bronze) 75%, #a7833a 100%);
    -webkit-background-clip: text; background-clip: text; color: transparent;
  }
  .front-subtitle {
    position: absolute; left: 215px; width: 200px; top: 247px; text-align: center;
    font-family: "Cinzel", serif; font-size: 20px; line-height: 24px;
    letter-spacing: .5px; color: var(--ink-dark);
  }
  .front-tagline {
    position: absolute; left: 0; width: 451px; top: 543px; text-align: center;
    font-family: "Cinzel", serif; font-size: 16.5px; line-height: 24px;
    letter-spacing: 2.2px; color: var(--ink-gold);
  }
  .front-author {
    position: absolute; left: 0; width: 451px; top: 617px; text-align: center;
    font-family: "Crimson Text", serif; font-size: 16px; letter-spacing: 2px;
    color: var(--ink-gold);
  }
</style>
</head>
<body>
<main class="canvas">
  <section class="cover-spread">
    <div class="light-backdrop" role="img" aria-label="Warm golden rays of light streaming from the upper right across an amber and brown sky"></div>

    <div class="back-cover">
      <h2 class="back-title">FAITH</h2>
      <p class="back-subtitle">ROAD <span class="connector">of</span> ENDLESS GRACE</p>
      <div class="back-blurb">
        <p>Lorem ipsum dolor sit amet, consectetur adipiscing elit, sed do eiusmod tempor incididunt ut labore et dolore magna aliqua. Quis ipsum suspendisse ultrices gravida. Risus commodo viverra maecenas accumsan lacus vel facilisis. Lorem ipsum dolor sit amet, consectetur adipiscing elit, sed do eiusmod tempor incididunt ut labore et dolore magna aliqua. Quis ipsum suspendisse ultrices gravida. Risus commodo viverra maecenas accumsan lacus vel facilisis.</p>
        <p>Lorem ipsum dolor sit amet, consectetur adipiscing elit, sed do eiusmod tempor incididunt ut labore et dolore magna aliqua. Quis ipsum suspendisse ultrices gravida. Risus commodo viverra maecenas accumsan lacus vel facilisis. Lorem ipsum dolor sit amet, consectetur adipiscing elit, sed do eiusmod tempor incididunt ut labore et dolore magna aliqua. Quis ipsum suspendisse ultrices gravida.</p>
      </div>
    </div>

    <div class="spine">
      <p class="spine-title"><span class="spine-main">FAITH</span> ROAD <span class="connector">of</span> ENDLESS GRACE</p>
      <p class="spine-author">Dr. Meral Hadwin</p>
    </div>

    <div class="front-cover">
      <h1 class="front-title">FAITH</h1>
      <p class="front-subtitle">ROAD <span class="connector">of</span> ENDLESS GRACE</p>
      <p class="front-tagline">GUIDE TO CULTIVATING INNER PEACE<br>AND MINDFUL LIVING</p>
      <p class="front-author">Dr. Meral Hadwin</p>
    </div>
  </section>
</main>
</body>
</html>
```